Quorbelline.io - Please redesign to make it look better from current design

We already have the current website, that you can access but we think it can improve from current version.
Quorbelline is a cryptocurrency hedge fund that allow you to participate in the hedge fund with cryptocurrency such as eth.
At current phase, we are doing an ICO, then we want to make sure that the website it looks professional, beautiful and trustable enough for investors after looking at our website.
Target Market(s)
Investors
Industry/Entity Type
Investment
Coding
Coded - Design and coding required
Number of Pages Required
1 page
Look and feel
Each slider illustrates characteristics of the customer's brand and the style your logo design should communicate.

```html
<!DOCTYPE html>
<html lang="en">
<head>
<meta charset="utf-8">
<title>Quorbelline – Digital Asset Management</title>
<link rel="stylesheet" href="https://fonts.googleapis.com/css2?family=Quicksand:wght@300;400&family=Roboto:wght@300;400;500;700&family=Open+Sans:ital,wght@0,400;1,400&display=swap">
<style>
:root{
  --brand:#15278c;
  --brand-dark:#0f1f78;
  --ink:#222;
  --muted:#555;
  --grey-band:#eeeeee;
  --card:#ffffff;
  --sky:#c8eefc;
  --line:#d6d6d6;
  --white:#ffffff;
}
*{box-sizing:border-box;margin:0;padding:0}
html,body{width:1200px;height:2875px;overflow:hidden}
body{position:relative;background:var(--white);font-family:"Open Sans",sans-serif;color:var(--ink)}
.abs{position:absolute}
h1,h2,h3,h4{font-weight:400}

/* header */
.site-logo{left:77px;top:30px;display:flex;align-items:center;gap:12px;font-family:"Roboto",sans-serif;font-weight:500;font-size:24px;color:var(--brand)}
.site-logo .dot{width:34px;height:34px;border-radius:50%;background:var(--brand)}
.main-nav{top:52px;left:0;width:1200px;font-family:"Roboto",sans-serif;font-size:17px;color:#111}
.main-nav a{position:absolute;color:inherit;text-decoration:none}

/* hero */
.hero-art{left:640px;top:120px;width:560px;height:551px;background:radial-gradient(ellipse at 55% 50%,#e8ecfb 0%,#f7f8fe 60%,#ffffff 100%)}
.hero-title{left:78px;top:246px;font-family:"Quicksand",sans-serif;font-weight:300;font-size:80px;color:var(--brand);letter-spacing:1px;line-height:1;z-index:1}
.hero-sub{left:79px;top:360px;font-family:"Roboto",sans-serif;font-weight:300;font-size:38px;color:var(--brand);z-index:1}
.hero-rule{left:80px;top:436px;width:58px;height:2px;background:var(--brand)}
.hero-text{left:80px;top:462px;width:540px;font-size:18px;line-height:29px;color:var(--muted);z-index:1}

/* team */
.team-band{left:0;top:671px;width:1200px;height:562px;background:var(--grey-band)}
.section-title{left:0;width:1200px;text-align:center;font-family:"Roboto",sans-serif;font-weight:300;font-size:44px;color:#111}
.team-card{top:798px;width:320px;height:383px;background:var(--card);box-shadow:0 2px 6px rgba(0,0,0,.12)}
.team-card .photo{position:absolute;left:10px;top:17px;width:86px;height:86px;border-radius:50%;background:linear-gradient(160deg,#8a7a70,#3e3a44)}
.team-card .role{position:absolute;left:108px;top:33px;font-style:italic;font-size:16px;color:#333}
.team-card .name{position:absolute;left:108px;top:58px;font-family:"Roboto",sans-serif;font-size:18px;color:var(--brand)}
.team-card .divider{position:absolute;left:0;top:120px;width:100%;height:1px;background:#e4e4e4}
.team-card .bio{position:absolute;left:13px;top:136px;width:296px;font-size:15px;line-height:25px;color:#555}

/* about */
.about-text{left:200px;top:1340px;width:800px;text-align:center;font-size:15.5px;line-height:25px;color:#555}
.btn-primary{left:516px;top:1488px;width:166px;height:51px;background:var(--brand);color:var(--white);font-family:"Roboto",sans-serif;font-weight:700;font-size:16px;display:flex;align-items:center;justify-content:center}

/* process */
.process-band{left:0;top:1593px;width:1200px;height:418px;background:var(--brand)}
.process-title{left:80px;top:1642px;font-family:"Roboto",sans-serif;font-weight:300;font-size:42px;color:var(--white)}
.process-sub{left:80px;top:1730px;font-family:"Roboto",sans-serif;font-weight:400;font-size:28px;color:var(--white)}
.process-text{left:80px;top:1776px;width:560px;font-size:15.5px;line-height:25px;color:var(--white)}
.process-art{left:671px;top:1649px;width:336px;height:249px;background:linear-gradient(135deg,#2a3c9c,#1c2f90)}

/* distribution */
.dist-title{left:0;top:2058px;width:1200px;text-align:center;font-family:"Roboto",sans-serif;font-weight:400;font-size:29px;color:var(--brand)}
.dist-diagram{left:0;top:2011px;width:1200px;height:510px}
.dist-label{font-family:"Roboto",sans-serif;color:#222;font-size:20px;line-height:1.1}
.dist-label small{font-size:14px}
.dist-label .note{display:block;font-family:"Open Sans",sans-serif;font-size:14px;color:#444;margin-top:3px}
.dist-center{left:0;width:1200px;text-align:center}
.dist-remainder{left:0;top:2443px;width:1200px;text-align:center;font-size:17px;color:#222}

/* footer */
.footer-band{left:0;top:2521px;width:1200px;height:354px;background:var(--brand)}
.footer-head{top:2562px;font-family:"Roboto",sans-serif;font-weight:400;font-size:21px;color:var(--white)}
.footer-text{font-size:15.5px;line-height:23px;color:var(--white)}
.btn-light{left:79px;top:2718px;width:164px;height:52px;background:var(--sky);color:var(--brand-dark);font-family:"Roboto",sans-serif;font-weight:700;font-size:15px;display:flex;align-items:center;justify-content:center}
.contact-name{left:355px;top:2602px;display:flex;align-items:center;gap:12px;font-family:"Roboto",sans-serif;font-size:21px;letter-spacing:2px;color:var(--white)}
.newsletter-field{left:640px;top:2688px;width:270px;height:50px;background:var(--white);display:flex;align-items:center}
.newsletter-field span{padding-left:20px;font-size:14px;color:#777;flex:1}
.newsletter-field .send{width:50px;height:50px;background:var(--sky);display:flex;align-items:center;justify-content:center}
.footer-brand{left:955px;top:2568px;width:147px;text-align:center;font-family:"Roboto",sans-serif;font-size:20px;color:var(--white)}
.footer-brand .dot{width:90px;height:90px;border-radius:50%;background:var(--white);margin:0 auto 14px}
.social{top:2718px;width:40px;height:40px;border-radius:50%;border:2px solid var(--white);background:var(--sky)}
.footer-rule{left:79px;top:2812px;width:1042px;height:1px;background:rgba(255,255,255,.25)}
.copyright{left:0;top:2832px;width:1200px;text-align:center;font-family:"Roboto",sans-serif;font-size:17px;color:var(--white)}
.copyright b{font-weight:700}
</style>
</head>
<body>

<header>
  <div class="abs site-logo"><span class="dot"></span>quorbelline</div>
  <nav class="abs main-nav">
    <a href="#" style="left:640px">Home</a>
    <a href="#" style="left:732px">About</a>
    <a href="#" style="left:826px">Process</a>
    <a href="#" style="left:935px">Our Team</a>
    <a href="#" style="left:1058px">Contact</a>
  </nav>
</header>

<section class="hero">
  <div class="abs hero-art" role="img" aria-label="Line illustration of crypto assets, rocket, charts and payment icons joined in a network"></div>
  <h1 class="abs hero-title">quorbelline</h1>
  <h2 class="abs hero-sub">Digital Asset Management</h2>
  <div class="abs hero-rule"></div>
  <p class="abs hero-text">Quorbelline enable companies and investors to facilities business operation in modern digital world, including asset management on hedge fund strategy model.</p>
</section>

<section class="team">
  <div class="abs team-band"></div>
  <h2 class="abs section-title" style="top:716px">EXECUTIVE TEAM</h2>

  <article class="abs team-card" style="left:79px">
    <div class="photo" role="img" aria-label="Portrait of the director"></div>
    <div class="role">Director</div>
    <div class="name">Korvath Menlisar</div>
    <div class="divider"></div>
    <p class="bio">As a hedge fund manager. Menlisar is the Chief Executive Officer of Brismoor Capital LLC, an investment manager of Halvane Ridge Fund SP (Long-Short Equity Fund, investing in U.S. Stock Market) and Kestrune Fund (Managed Futures Fund, focusing in Japanese Futures Market) Both based in Tokyo.</p>
  </article>

  <article class="abs team-card" style="left:439px">
    <div class="photo" role="img" aria-label="Portrait of the technical advisor" style="background:linear-gradient(160deg,#b9c4b0,#5e6a58)"></div>
    <div class="role">Technical advisor</div>
    <div class="name">Tavin Oshelm</div>
    <div class="divider"></div>
    <p class="bio">Oshelm has various experienced on cryptocurrency and blockchain technology. He created what was the world's 4th most valuable cryptocurrency in February 2014. He is also the world's first person to implement stealth addresses in ZX-Vaults, improving cryptocurrency anonymity.</p>
  </article>

  <article class="abs team-card" style="left:800px">
    <div class="photo" role="img" aria-label="Portrait of the marketing consultant" style="background:linear-gradient(160deg,#a0522d,#3a1c14)"></div>
    <div class="role">Marketing Consultant</div>
    <div class="name">Ravek Danthorluen</div>
    <div class="divider"></div>
    <p class="bio">Danthorluen embeds a decade of experience in brand building, strategic planning, and marketing communication across the global agencies, such as Pelmont Worldgroup, KLRD, Ivo Brastel, Sorenkai. His seasoned specialty focuses on exploring a new market insight to formulate disruptive strategies</p>
  </article>
</section>

<section class="about">
  <h2 class="abs section-title" style="top:1274px">ABOUT US</h2>
  <p class="abs about-text">Quorbelline process and manages on hedge fund strategy models which invests in a diversified portfolio of blockchain tokens. Blockchain tokens are emerging which add a monetary incentive layer to p2p protocols and facilitate equity crowdfunding that anyone in the world can participate in. This means open source software developers can monetize their networks at the protocol level and users of the network are the equity owners of the network. For this conditions, returns will go to holders of the tokens.</p>
  <div class="abs btn-primary">EXPLORE MORE</div>
</section>

<section class="process">
  <div class="abs process-band"></div>
  <h2 class="abs process-title">PROCESS</h2>
  <h3 class="abs process-sub">Hedge Fund Model</h3>
  <p class="abs process-text">Quorbelline run on closed-end fund (CEF) model which offers its shares to investors and utilize the fund to speculate and invest in the innovative blockchain tokens. Quorbelline will charge an upfront annual operation fee 4% of the money raised during the ICO. After that, the fund will charge a quarterly performance of 50% on the net profit made.</p>
  <div class="abs process-art" role="img" aria-label="Illustration of a rising profit chart on a screen with gears"></div>
</section>

<section class="distribution">
  <h2 class="abs dist-title">Net Profit Distribution</h2>
  <svg class="abs dist-diagram" viewBox="0 2011 1200 510" width="1200" height="510" aria-hidden="true">
    <g fill="none" stroke="#d4d4d4" stroke-width="2">
      <line x1="600" y1="2205" x2="600" y2="2172"/>
      <line x1="460" y1="2172" x2="738" y2="2172"/>
      <polyline points="512,2266 447,2235 192,2235"/>
      <polyline points="690,2262 738,2235 1006,2235"/>
      <polyline points="546,2371 479,2400 192,2400"/>
      <polyline points="654,2371 719,2400 987,2400"/>
    </g>
    <polygon points="600,2205 690,2266 656,2371 544,2371 510,2266" fill="#c8eefc"/>
    <g fill="#15278c">
      <circle cx="600" cy="2205" r="4"/>
      <circle cx="690" cy="2266" r="4"/>
      <circle cx="656" cy="2371" r="4"/>
      <circle cx="544" cy="2371" r="4"/>
      <circle cx="510" cy="2266" r="4"/>
    </g>
    <text x="600" y="2300" text-anchor="middle" font-family="Roboto, sans-serif" font-size="16" font-weight="500" fill="#15278c">quorbelline</text>
  </svg>
  <div class="abs dist-center dist-label" style="top:2112px">50 %<span class="note">of net profit is distributed to investors</span></div>
  <div class="abs dist-label" style="left:215px;top:2173px">0 – 5 % <small>net profit</small> &gt; 0%<span class="note">performance fee</span></div>
  <div class="abs dist-label" style="left:784px;top:2173px">&gt; 15% <small>net profit</small> &gt; 15%<span class="note">performance fee</span></div>
  <div class="abs dist-label" style="left:253px;top:2343px">5 – 10% <small>net profit</small> &gt; 5%<span class="note">performance fee</span></div>
  <div class="abs dist-label" style="left:746px;top:2343px">10-15 % <small>net profit</small> &gt; 13%<span class="note">performance fee</span></div>
  <p class="abs dist-remainder">The remainder (50% minus performance fee, so at least 35%) is reinvested</p>
</section>

<footer>
  <div class="abs footer-band"></div>

  <h4 class="abs footer-head" style="left:80px">FOR MORE INFO</h4>
  <p class="abs footer-text" style="left:80px;top:2601px;width:230px">Lorem Ipsum is simply dummy text of the printing and typesetting industry. Lorem Ipsum has been the industry's.</p>
  <div class="abs btn-light">DOWNLOAD PDF</div>

  <h4 class="abs footer-head" style="left:355px">CONTACT INFO</h4>
  <div class="abs contact-name">
    <svg width="18" height="26" viewBox="0 0 18 26" aria-hidden="true"><path d="M9 0C4 0 0 4 0 9c0 7 9 17 9 17s9-10 9-17C18 4 14 0 9 0z" fill="#fff"/><circle cx="9" cy="9" r="3.5" fill="#15278c"/></svg>
    quorbelline
  </div>
  <p class="abs footer-text" style="left:387px;top:2648px;width:230px">Suites 04-12, 9B/F., East Wing, Meridan Trade Plaza, Lantern Quay, 42, Velmont Road, Tsim Sha Tsui, Kowloon, Hong Kong.</p>

  <h4 class="abs footer-head" style="left:640px">NEWSLETTER</h4>
  <p class="abs footer-text" style="left:640px;top:2601px;width:265px">Subscribe to Our Newsletter to get latest News &amp; Updates About Company</p>
  <div class="abs newsletter-field">
    <span>Enter Your E-Mail</span>
    <div class="send"><svg width="22" height="22" viewBox="0 0 24 24" aria-hidden="true"><path d="M2 11 22 2 15 22 11 13z" fill="none" stroke="#15278c" stroke-width="2" stroke-linejoin="round"/><line x1="11" y1="13" x2="22" y2="2" stroke="#15278c" stroke-width="2"/></svg></div>
  </div>

  <div class="abs footer-brand"><div class="dot"></div>quorbelline</div>
  <span class="abs social" style="left:957px"></span>
  <span class="abs social" style="left:1009px"></span>
  <span class="abs social" style="left:1059px"></span>

  <div class="abs footer-rule"></div>
  <p class="abs copyright">© <b>quorbelline</b> - 2017. All Rights Reserved.</p>
</footer>

</body>
</html>
```